The Vantor Codex Book Cover

"The Vantor Codex" is a book I wrote with the slogan "Unlock Performance, Spark Engagement: Master the Art of Building Winning Cultures in Today's Hybrid World". The book is designed around a methodology that's mine and that I attached. I would love to see the graphic of the methodology integrated in the design in a very subtle way. Use colors from the model but the book cover should be catchy, modern and engaging to the eye.
Overall the book is about three key elements towards success:
- (Self) Directions (purpose)
- Human experience (people and psychological safety)
- Maximize engagement
The methodology is a FLOW so flow is something that could be incorporated as well in the concept.
Low design quality
Managers and Teams

```html
<!DOCTYPE html>
<html lang="en">
<head>
<meta charset="utf-8">
<title>The Vantor Codex — Book Cover</title>
<link rel="stylesheet" href="https://fonts.googleapis.com/css2?family=Cinzel:wght@400&family=Bebas+Neue&family=Oswald:wght@500&display=swap">
<style>
  :root {
    --backdrop: #7f8796;
    --cover: #030303;
    --ink: #f4f4f4;
    --rule: #d9d9d9;
    --trail-violet: #8a6cf0;
    --trail-teal: #4fc3e8;
    --trail-green: #7cc46a;
    --trail-gold: #e0a84a;
  }
  * { margin: 0; padding: 0; box-sizing: border-box; }
  html, body { width: 1200px; height: 1122px; overflow: hidden; }
  body {
    background: var(--backdrop);
    display: flex;
    align-items: center;
    justify-content: center;
  }
  .cover {
    position: relative;
    width: 760px;
    height: 1060px;
    background: var(--cover);
    color: var(--ink);
    text-align: center;
    overflow: hidden;
  }
  .author {
    position: absolute;
    top: 118px;
    left: 0; right: 0;
    font-family: "Cinzel", serif;
    font-size: 42px;
    letter-spacing: 3px;
  }
  .title {
    position: absolute;
    top: 188px;
    left: 0; right: 0;
    font-family: "Bebas Neue", sans-serif;
    font-weight: 400;
    line-height: 0.9;
  }
  .title-top { display: block; font-size: 74px; letter-spacing: 1px; }
  .title-main { display: block; font-size: 150px; letter-spacing: 2px; }
  .tagline {
    position: absolute;
    top: 405px;
    left: 150px; right: 150px;
  }
  .tagline-rule { height: 2px; background: var(--rule); }
  .tagline-lead {
    font-family: "Oswald", sans-serif;
    font-size: 13px;
    letter-spacing: 5px;
    text-transform: uppercase;
    padding: 7px 0 6px;
  }
  .tagline-body {
    margin-top: 8px;
    font-family: "Cinzel", serif;
    font-size: 15px;
    line-height: 1.3;
  }
  .flow-art {
    position: absolute;
    top: 530px;
    left: 60px;
    width: 640px;
    height: 340px;
    background:
      radial-gradient(ellipse 22% 32% at 18% 72%, var(--trail-gold) 0%, transparent 100%),
      linear-gradient(100deg,
        var(--trail-gold) 0%,
        var(--trail-violet) 22%,
        var(--trail-teal) 48%,
        var(--trail-green) 70%,
        var(--trail-teal) 92%);
    -webkit-mask-image: radial-gradient(ellipse 50% 50% at 50% 50%, #000 30%, transparent 100%);
    mask-image: radial-gradient(ellipse 50% 50% at 50% 50%, #000 30%, transparent 100%);
    opacity: 0.5;
  }
  .editor {
    position: absolute;
    top: 912px;
    left: 0; right: 0;
    font-family: "Cinzel", serif;
    font-size: 48px;
    letter-spacing: 2px;
  }
</style>
</head>
<body>
  <main class="cover">
    <p class="author">Author Name</p>
    <h1 class="title">
      <span class="title-top">The Vantor</span>
      <span class="title-main">Codex</span>
    </h1>
    <div class="tagline">
      <div class="tagline-rule"></div>
      <p class="tagline-lead">Unlock Performance, Spark Engagement:</p>
      <div class="tagline-rule"></div>
      <p class="tagline-body">Master the Art of Building Winning Cultures<br>in Today's Hybrid World</p>
    </div>
    <div class="flow-art" role="img" aria-label="Multicoloured light trails flowing in an infinity loop in gold, violet, teal and green"></div>
    <p class="editor">Editor</p>
  </main>
</body>
</html>
```